QP Fiduciary Website Redesign Contest

We want to refresh our website to be more insitutional, professional for an international audience. We have designed a new logo for this purpose and that has been attached. A full brand brief and positioning statement has also been attached. Please read through all the documents carefully before designing. The old website is found here: https://qp-fiduciary.example/

Target Market(s)

Actuaries and associated businesses internationally

Industry/Entity Type

professional services - actuaries

Number of Pages Required

3 page

Font styles to use
Sans Serif

Colors
0054AA
0677BA
7BADD7
CADEEF
E8F1F8
0094D4
00A9DD
6FCCEA
C7EBF8
E9F6FB
F0912C
F2A743
F7CA91
FBE8D2
FDF5EE
EE7325
F08F49
F5BC92
FAE3D3
FDF4ED
EB3D1F
EC4F4E
F09395
F8D3D4
FCEDEE

Requirements
Must have
• blues and greens to match the logo color, complimentary colors, navigation
Nice to have
• old site: https://qp-fiduciary.example/

```html
<!DOCTYPE html>
<html lang="en">
<head>
<meta charset="utf-8">
<title>QP Fiduciary — Actuarial Software</title>
<link href="https://fonts.googleapis.com/css2?family=Arimo:wght@400;500;600;700&display=swap" rel="stylesheet">
<style>
:root{
  --blue:#0054AA;
  --blue-deep:#0a4ea6;
  --blue-card:#0a5ab2;
  --blue-light:#7BADD7;
  --green:#14A97F;
  --green-text:#1cbf8c;
  --orange:#EE7325;
  --ink:#1d1d1f;
  --muted:#333;
  --line:#dcdfe4;
  --white:#fff;
}
*{box-sizing:border-box;margin:0;padding:0}
html,body{width:1200px;height:3805px;overflow:hidden}
body{font-family:"Arimo",Arial,sans-serif;color:var(--ink);background:var(--white);position:relative}
.abs{position:absolute}
.center{left:0;width:1200px;text-align:center}

/* nav */
.nav{position:absolute;top:0;left:0;width:1200px;height:93px;background:var(--white)}
.brand{position:absolute;left:49px;top:30px;display:flex;align-items:center;gap:10px;font-weight:700;font-size:24px;letter-spacing:1px;color:var(--blue)}
.brand .dot{width:14px;height:14px;border-radius:50%;background:var(--orange)}
.nav-link{position:absolute;top:36px;font-size:15px;color:var(--ink)}
.nav-link.active{color:var(--orange);font-weight:600}
.btn-outline{position:absolute;border:1.5px solid var(--orange);color:var(--orange);border-radius:22px;font-size:15px;display:flex;align-items:center;justify-content:center;gap:8px;background:var(--white)}
.btn-solid{position:absolute;background:var(--orange);color:var(--white);border-radius:22px;font-size:15px;display:flex;align-items:center;justify-content:center;gap:10px}

/* hero */
.hero{position:absolute;top:93px;left:0;width:1200px;height:508px;
  background:linear-gradient(135deg,#0b57b4 0%,#0a4fa8 45%,#1766c4 70%,#0a4ba2 100%)}
.hero h1{position:absolute;top:102px;font-size:45px;font-weight:400;color:var(--white);line-height:55px}
.hero h1 .accent{color:var(--green-text);font-weight:700}
.hero p{position:absolute;top:236px;font-size:18px;line-height:31px;color:var(--white)}

/* overview */
.section-title{font-size:40px;font-weight:500;color:var(--blue)}
.overview-text{position:absolute;left:223px;width:756px;top:766px;font-size:15px;line-height:31px;text-align:justify;text-align-last:center;color:var(--muted)}
.overview-card{position:absolute;left:185px;top:876px;width:830px;height:627px;border:1px solid var(--line);border-radius:6px;background:var(--white)}
.divider-v{position:absolute;left:413px;top:22px;width:1px;height:580px;background:var(--line)}
.divider-h{position:absolute;left:29px;top:306px;width:772px;height:1px;background:var(--line)}
.feature{position:absolute;width:300px;text-align:center}
.feature svg{display:block;margin:0 auto}
.feature h3{font-size:17px;font-weight:500;margin-top:20px}
.feature p{font-size:15px;line-height:31px;margin-top:16px;color:var(--muted)}
.badge{position:absolute;left:365px;top:256px;width:100px;height:100px;background:var(--white);border-radius:8px;box-shadow:0 6px 18px rgba(0,0,0,.12);display:flex;align-items:center;justify-content:center;font-size:26px;font-weight:700;color:var(--blue)}

/* solutions */
.solutions{position:absolute;top:1592px;left:0;width:1200px;height:802px;background:linear-gradient(135deg,#0a56b0,#0a4aa0)}
.solutions h2{position:absolute;top:82px;font-size:40px;font-weight:500;color:var(--white)}
.solutions h2 span{color:var(--green-text)}
.solutions .lead{position:absolute;top:158px;font-size:15px;line-height:31px;color:var(--white)}
.solution{position:absolute;left:183px;width:834px;height:127px;background:var(--blue-card);border-radius:5px;color:var(--white);box-shadow:0 6px 14px rgba(0,20,70,.25)}
.solution::before{content:"";position:absolute;left:0;top:10px;bottom:10px;width:5px;background:var(--blue-light);border-radius:2px}
.solution.active{background:var(--green)}
.solution.active::before{background:var(--white);top:0;bottom:0}
.solution h3{position:absolute;left:57px;top:28px;font-size:17px;font-weight:600}
.solution p{position:absolute;left:57px;top:72px;font-size:15px}
.solution .go{position:absolute;right:30px;top:54px}
.solution.active .go{right:20px;top:55px;width:50px;height:50px;background:var(--white);border-radius:6px;display:flex;align-items:center;justify-content:center}

/* insights */
.insights-lead{position:absolute;top:2549px;font-size:15px;line-height:31px;color:var(--muted)}
.insight{position:absolute;top:2660px;width:316px;height:432px;background:var(--white);border-radius:4px;box-shadow:0 6px 22px rgba(0,0,0,.08);text-align:center}
.insight.featured{border:1.5px solid var(--orange);box-shadow:0 14px 30px rgba(0,0,0,.12)}
.insight svg{position:absolute;left:118px;top:40px}
.insight h3{position:absolute;left:0;width:100%;top:146px;font-size:17px;font-weight:500;line-height:31px}
.insight p{position:absolute;left:36px;width:244px;top:221px;font-size:15px;line-height:31px;color:var(--muted);text-align:justify;text-align-last:center}
.insight .btn-outline,.insight .btn-solid{left:81px;top:345px;width:154px;height:39px}
.arrow{position:absolute;top:2866px}

/* cta */
.cta{position:absolute;top:3192px;left:0;width:1200px;height:392px;background:linear-gradient(135deg,#0b57b4,#0a4ca2)}
.cta h2{position:absolute;top:82px;font-size:40px;font-weight:500;color:var(--white)}
.cta h2 span{color:var(--green-text)}
.cta p{position:absolute;top:158px;font-size:15px;line-height:31px;color:var(--white)}

/* footer */
.footer-brand{position:absolute;left:114px;top:3645px;display:flex;align-items:center;gap:14px;font-size:38px;font-weight:700;letter-spacing:1.5px;color:var(--blue)}
.footer-brand .dot{width:20px;height:20px;border-radius:50%;background:var(--orange)}
.quick-title{position:absolute;left:575px;top:3641px;font-size:18px;font-weight:600;color:var(--blue)}
.quick-link{position:absolute;top:3686px;font-size:15px}
.footer-line{position:absolute;left:98px;top:3733px;width:1007px;height:1px;background:var(--line)}
.legal{position:absolute;top:3759px;font-size:13px;color:var(--muted)}
</style>
</head>
<body>

<header class="nav">
  <div class="brand"><span class="dot"></span>QP FIDUCIARY</div>
  <a class="nav-link active" style="left:327px">Home</a>
  <a class="nav-link" style="left:405px">Platform</a>
  <a class="nav-link" style="left:498px">Solutions</a>
  <a class="nav-link" style="left:596px">Insights</a>
  <a class="nav-link" style="left:684px">Company</a>
  <a class="nav-link" style="left:785px">Contact</a>
  <a class="btn-outline" style="left:887px;top:27px;width:260px;height:40px">Request Technical Walkthrough</a>
</header>

<section class="hero" role="img" aria-label="Deep blue abstract background of translucent overlapping panels">
  <h1 class="center">Actuarial Software for Structured,<br><span class="accent">Auditable Financial Analysis.</span></h1>
  <p class="center">QP Fiduciary develops software that translates established actuarial methodologies<br>into disciplined, decision-ready tools.</p>
  <a class="btn-solid" style="left:455px;top:336px;width:290px;height:38px">Request Technical Walkthrough
    <svg width="14" height="12" viewBox="0 0 14 12"><path d="M1 6h11M7 1l5 5-5 5" fill="none" stroke="#fff" stroke-width="1.6"/></svg></a>
</section>

<h2 class="section-title abs center" style="top:690px">Platform Overview</h2>
<p class="overview-text">QP Fiduciary's software platform transforms established actuarial methodologies into modular, decision ready tools for reserving, valuation, pricing, and risk analysis across diverse regulatory environments.</p>

<div class="overview-card">
  <div class="divider-v"></div>
  <div class="divider-h"></div>
  <div class="feature" style="left:57px;top:46px">
    <svg width="60" height="54" viewBox="0 0 60 54" fill="none" stroke="#14A97F" stroke-width="2"><rect x="2" y="2" width="44" height="40" rx="2"/><path d="M9 12h14M9 20h8M9 28h14M28 20h10M34 20v12"/><circle cx="48" cy="20" r="5"/><circle cx="36" cy="44" r="5"/></svg>
    <h3>Structured Workflows</h3>
    <p>Modular processes designed for all multi-jurisdictional reviews and efficient actuarial analysis.</p>
  </div>
  <div class="feature" style="left:457px;top:46px">
    <svg width="60" height="54" viewBox="0 0 60 54" fill="none" stroke="#14A97F" stroke-width="2"><path d="M4 8h40v32H16l-8 8v-8H4z"/><path d="M11 18h26M11 25h26M11 32h18"/><circle cx="50" cy="6" r="5" fill="#14A97F"/></svg>
    <h3>Transparency of Assumptions</h3>
    <p>Clear visibility into several assets and methodological inputs made for clarity and understanding.</p>
  </div>
  <div class="feature" style="left:57px;top:358px">
    <svg width="60" height="54" viewBox="0 0 60 54" fill="none" stroke="#14A97F" stroke-width="3"><path d="M4 2v48h50"/><path d="M16 42V30M26 42V20M36 42V32M46 42v-4"/></svg>
    <h3>Auditability</h3>
    <p>Governance-ready outputs and systems which help ensuring full traceability and compliance.</p>
  </div>
  <div class="feature" style="left:457px;top:358px">
    <svg width="60" height="62" viewBox="0 0 60 62" fill="none" stroke="#14A97F" stroke-width="2"><path d="M4 14L28 2l24 12zM6 18h44M12 22v22M22 22v22M32 22v16M4 48h30"/><circle cx="48" cy="48" r="10" fill="#14A97F" stroke="none"/><path d="M43 48l4 4 6-7" stroke="#fff"/></svg>
    <h3>Governance</h3>
    <p>Disciplined tools supporting the judgments across various types of regulatory environments.</p>
  </div>
  <div class="badge">QP</div>
</div>

<section class="solutions">
  <h2 class="center">Core <span>Solutions</span></h2>
  <p class="lead center">QP Fiduciary offers specialized software solutions for actuaries and risk professionals. Each module<br>supports structured workflows across reserving, valuation, pricing, and enterprise risk management.</p>
  <div class="solution active" style="top:291px">
    <h3>Reserving &amp; Valuation:</h3>
    <p>Software for structured reserving workflows and financial reporting across jurisdictions.</p>
    <span class="go"><svg width="20" height="20" viewBox="0 0 20 20"><path d="M2 18L18 2M7 2h11v11" fill="none" stroke="#EE7325" stroke-width="1.6"/></svg></span>
  </div>
  <div class="solution" style="top:428px">
    <h3>Pricing:</h3>
    <p>Software for insurance and reinsurance pricing models based on actuarial methodologies.</p>
    <span class="go"><svg width="20" height="20" viewBox="0 0 20 20"><path d="M2 18L18 2M7 2h11v11" fill="none" stroke="#fff" stroke-width="1.6"/></svg></span>
  </div>
  <div class="solution" style="top:566px">
    <h3>Enterprise Risk Management:</h3>
    <p>Software for reinsurance optimization and capital modeling strategies.</p>
    <span class="go"><svg width="20" height="20" viewBox="0 0 20 20"><path d="M2 18L18 2M7 2h11v11" fill="none" stroke="#fff" stroke-width="1.6"/></svg></span>
  </div>
</section>

<h2 class="section-title abs center" style="top:2472px">Thought Leadership</h2>
<p class="insights-lead center">Explore practitioner-level articles on actuarial methods and governance.<br>Insights into multi-jurisdictional practice and regulatory challenges.</p>

<svg class="arrow" style="left:40px" width="26" height="24" viewBox="0 0 26 24"><path d="M25 12H2M12 2L2 12l10 10" fill="none" stroke="#888" stroke-width="1.6"/></svg>
<svg class="arrow" style="left:1130px" width="26" height="24" viewBox="0 0 26 24"><path d="M1 12h23M14 2l10 10-10 10" fill="none" stroke="#EE7325" stroke-width="1.6"/></svg>

<article class="insight" style="left:111px">
  <svg width="80" height="80" viewBox="0 0 80 80" fill="none" stroke="#14A97F" stroke-width="3.5"><path d="M6 34v14M18 24v20M30 4v28M42 20v12"/><path d="M6 70l18-20 14 12 26-22"/><path d="M52 40h12v12"/></svg>
  <h3>Observations on Actuarial<br>Practice in Emerging Markets</h3>
  <p>Analyzes multi-jurisdictional key challenges and best practices for global actuarial workflows.</p>
  <a class="btn-outline">Read More <svg width="12" height="10" viewBox="0 0 12 10"><path d="M0 5h10M6 1l4 4-4 4" fill="none" stroke="#EE7325" stroke-width="1.5"/></svg></a>
</article>
<article class="insight featured" style="left:443px">
  <svg width="80" height="80" viewBox="0 0 80 80" fill="none" stroke="#14A97F" stroke-width="3"><path d="M6 8l12 12M18 8L6 20M58 60l12 12M70 60L58 72"/><path d="M50 12h16v16"/><path d="M66 12C40 14 52 40 34 46 24 50 18 56 18 62"/><circle cx="14" cy="66" r="6"/></svg>
  <h3>Methodological Perspectives<br>in Actuarial Reserving</h3>
  <p>Explores structured approaches to reserving calculations and their evolution in modern practice.</p>
  <a class="btn-solid">Read More <svg width="12" height="10" viewBox="0 0 12 10"><path d="M0 5h10M6 1l4 4-4 4" fill="none" stroke="#fff" stroke-width="1.5"/></svg></a>
</article>
<article class="insight" style="left:773px">
  <svg width="80" height="80" viewBox="0 0 80 80" fill="none" stroke="#14A97F" stroke-width="3.5"><path d="M4 22L40 4l36 18zM4 26h72M16 32v32M32 32v32M48 32v32M64 32v32M4 70h72"/></svg>
  <h3>Governance Considerations in<br>Multi-Jurisdictional Analysis</h3>
  <p>Examines governance various frameworks ensuring compliance across regulatory environments.</p>
  <a class="btn-outline">Read More <svg width="12" height="10" viewBox="0 0 12 10"><path d="M0 5h10M6 1l4 4-4 4" fill="none" stroke="#EE7325" stroke-width="1.5"/></svg></a>
</article>

<section class="cta">
  <h2 class="center">Interested in <span>Exploring the Platform?</span></h2>
  <p class="center">Interested in exploring our actuarial software platform?<br>Request a technical walkthrough to discuss your structured analysis needs.</p>
  <a class="btn-solid" style="left:455px;top:255px;width:290px;height:38px">Request Technical Walkthrough
    <svg width="14" height="12" viewBox="0 0 14 12"><path d="M1 6h11M7 1l5 5-5 5" fill="none" stroke="#fff" stroke-width="1.6"/></svg></a>
</section>

<footer>
  <div class="footer-brand"><span class="dot"></span>QP FIDUCIARY</div>
  <div class="quick-title">Quick Links</div>
  <a class="quick-link" style="left:575px">Home</a>
  <a class="quick-link" style="left:650px">Platform</a>
  <a class="quick-link" style="left:742px">Solutions</a>
  <a class="quick-link" style="left:841px">Insights</a>
  <a class="quick-link" style="left:929px">Company</a>
  <a class="quick-link" style="left:1030px">Contact</a>
  <div class="footer-line"></div>
  <p class="legal" style="left:112px">©Copyright 2026 QP Fiduciary. All Rights Reserved.</p>
  <p class="legal" style="left:919px">Privacy Policy &nbsp;&nbsp; | &nbsp;&nbsp; Terms</p>
</footer>

</body>
</html>
```